Flyer-Design für Open Workspace Lösung
Zielgruppe
Was machen wir? Open Workspace Lösung für Ärzte und Psychotherapeuten.
Zielgruppe: Unser Angebot richtet sich an Ärzte, Psychologen, Psychotherapeuten, Heilpraktiker für Psychotherapie (HeilprG) sowie Coaches und Supervisoren mit vergleichbarem und zertifiziertem Hintergrund. Darüber hinaus stehen die Räume auch für Seminare, Workshops oder Gruppenangebote zur Verfügung.
Aufgabenstellung
1. Die Word-Skizze ist ein Entwurf, der gerne verändert werden kann.
2. Das Foto in der oberen Hälfte ist ein Platzhalter. Es ist zwar real aber wir haben leider noch kein gutes Foto der fertigen Räume. Daher sollte, falls ein Bild verwendet wird, eine bearbeitbare Version mitgeliefert werden, damit wir das Bild noch austauschen können. Es muss kein Bild im Flyer verwendet werden, kann aber.
3. Unser Logo sollte auf den Flyer kommen. Es gibt das Logo mit und ohne Text. Beide hängen wir als Datei mit an.
4. Wir haben eine Website: www.praxis-sonnenquell.de
Der Flyer sollte zu dieser passen. Die Schriftart der Website ist font-famliy: 'Lato', sans-serif und sollte verwendet werden.
5. Die Farbe (türkis) ist vorgegeben. Die Definition ist: #0CE0AE
Die Grautöne der Website sind folgende: #444444, #555444, #5A5A5A, #888888, #CCCCCC #F4F4F4
6. wir hätten gerne einen one-pager, den man als Werbung an Emails anhängen und im Internet veröffentlichen kann und einen Flyer, der ausgedruckt ausliegen kann

```html
<!DOCTYPE html>
<html lang="de">
<head>
<meta charset="utf-8">
<title>Praxis am Sonnenquell – Flyer &amp; One-Pager</title>
<link href="https://fonts.googleapis.com/css2?family=Lato:ital,wght@0,300;0,400;0,700;0,900;1,400;1,700;1,900&display=swap" rel="stylesheet">
<style>
:root{
  --mint:#5cbd9d;
  --mint-dark:#4aa888;
  --mint-soft:#8fd3bb;
  --mint-pale:#eaf5f0;
  --mint-frame:#cfe9df;
  --ink:#444444;
  --ink-2:#5a5a5a;
  --grey:#888888;
  --stage:#e6e6e6;
  --paper:#ffffff;
}
*{box-sizing:border-box;margin:0;padding:0}
html,body{width:1200px;height:2979px;overflow:hidden}
body{background:var(--paper);font-family:'Lato',sans-serif;color:var(--ink);position:relative}
.abs{position:absolute}
.stage{left:0;top:0;width:1200px;height:912px;background:var(--stage)}
.sheet{background:var(--paper);box-shadow:0 4px 14px rgba(0,0,0,.18);overflow:hidden}
.brand{display:flex;align-items:center;gap:10px;color:var(--ink-2);font-weight:300;letter-spacing:.08em;text-transform:uppercase;line-height:1.05}
.brand-mark{flex:none;background:var(--mint)}
.photo{background:linear-gradient(160deg,#f7f8f6 0%,#e4e6e3 45%,#c9ccc9 100%)}
.photo-room{background:linear-gradient(150deg,#f3f2ee 0%,#d8d6cf 55%,#a59f93 100%)}
.photo-seminar{background:linear-gradient(150deg,#eeeeec 0%,#cfcac2 50%,#9c9488 100%)}
.map{background:linear-gradient(135deg,#ececec,#dcdcdc)}
.hl{color:var(--mint);font-weight:700}
.it{font-style:italic}
h3{font-weight:900;color:var(--ink)}
.small{font-size:8px;line-height:1.5;color:var(--ink-2)}
.box{background:var(--mint-pale)}
.room-card{display:flex;background:var(--mint);color:#fff}
.room-card .txt{padding:6px 8px}
.room-card .name{font-weight:900;font-size:12px}
.room-card .feat{font-style:italic;font-size:8px;line-height:1.35;color:#e4f6ef;margin-top:3px}
.room-card .price{font-weight:900;font-size:12px;margin-top:4px}
ul.list{list-style:none}
ul.list li{position:relative;padding-left:7px;margin-bottom:6px}
ul.list li::before{content:"•";position:absolute;left:0}
.banner{background:var(--mint);color:#fff;font-weight:900;clip-path:polygon(0 0,100% 0,94% 100%,0 100%)}
</style>
</head>
<body>

<!-- Cover panel, shown flat -->
<div class="abs stage">
  <div class="abs sheet" style="left:465px;top:80px;width:272px;height:560px">
    <div class="abs brand" style="left:24px;top:34px;font-size:15px;width:220px">
      <span class="brand-mark" style="width:30px;height:30px"></span>
      <span>Praxis am<br>Sonnenquell</span>
    </div>
    <div class="abs it" style="left:24px;top:100px;font-size:17px;font-weight:700;color:var(--ink);line-height:1.2">Flexible Raummiete<br>im Herzen von München</div>
    <div class="abs photo" role="img" aria-label="Foto: heller Therapieraum mit zwei grauen Sesseln und Blumenvase" style="left:0;top:160px;width:272px;height:250px"></div>
    <svg class="abs" style="left:0;top:360px" width="272" height="200" viewBox="0 0 272 200">
      <polygon points="0,30 272,0 272,200 0,200" fill="#8fd3bb"/>
      <polygon points="0,110 272,60 272,200 0,200" fill="#5cbd9d"/>
      <polygon points="0,30 140,110 0,110" fill="#a9ddca"/>
    </svg>
    <div class="abs it" style="right:18px;top:490px;text-align:right;font-size:10px;color:#fff;line-height:1.4">Lindenweg 22<br>80337 München<br>kontakt@praxis-sonnenquell.de</div>
  </div>
</div>

<!-- Outside spread -->
<div class="abs sheet" style="left:72px;top:997px;width:540px;height:573px">
  <div class="abs" style="left:8px;top:8px;width:256px;height:557px;border:2px solid var(--mint-frame)"></div>
  <div class="abs" style="left:24px;top:24px;width:230px;font-size:12px;line-height:1.45;font-style:italic;color:var(--ink)">
    <b>Bei Fragen</b>, für weitere Informationen oder zur <b>Vereinbarung einer Besichtigung</b> - gerne auch virtuell über Video - kontaktieren Sie uns:
  </div>
  <div class="abs box" style="left:16px;top:108px;width:240px;height:132px;padding:10px 8px;font-size:10px;line-height:1.6">
    <div class="hl it" style="font-size:12px">Carla Brenner-Voss</div>
    <div class="it">Email: kontakt@praxis-sonnenquell.de</div>
    <div class="it">Tel.: 0176 40218857</div>
    <div class="hl it" style="font-size:12px;margin-top:8px">Tobias Voss</div>
    <div class="it">Email: kontakt@praxis-sonnenquell.de</div>
    <div class="it">Tel.: 0177 3095126</div>
  </div>
  <div class="abs" style="left:28px;top:258px;width:214px;height:2px;background:var(--mint-frame)"></div>
  <div class="abs brand" style="left:28px;top:282px;font-size:16px">
    <span class="brand-mark" style="width:26px;height:26px"></span><span>Praxis am<br>Sonnenquell</span>
  </div>
  <div class="abs" style="left:28px;top:330px;font-size:11px;line-height:1.45;color:var(--ink)">Lindenweg 22<br>80337 München<br>kontakt@praxis-sonnenquell.de<br>www.praxis-sonnenquell.de</div>
  <div class="abs map" role="img" aria-label="Stadtplanausschnitt mit Standortmarkierung" style="left:28px;top:404px;width:214px;height:144px"></div>

  <div class="abs" style="left:270px;top:0;width:270px;height:573px">
    <div class="abs brand" style="left:24px;top:30px;font-size:15px">
      <span class="brand-mark" style="width:30px;height:30px"></span><span>Praxis am<br>Sonnenquell</span>
    </div>
    <div class="abs it" style="left:24px;top:208px;font-size:17px;font-weight:700;line-height:1.2">Flexible Raummiete<br>im Herzen von München</div>
    <div class="abs photo" role="img" aria-label="Foto: heller Therapieraum mit zwei grauen Sesseln und Blumenvase" style="left:0;top:260px;width:270px;height:190px"></div>
    <svg class="abs" style="left:0;top:413px" width="270" height="160" viewBox="0 0 270 160">
      <polygon points="0,25 270,0 270,160 0,160" fill="#8fd3bb"/>
      <polygon points="0,90 270,50 270,160 0,160" fill="#5cbd9d"/>
      <polygon points="0,25 130,90 0,90" fill="#a9ddca"/>
    </svg>
    <div class="abs it" style="right:14px;top:490px;text-align:right;font-size:10px;color:#fff;line-height:1.45">Lindenweg 22<br>80337 München<br>kontakt@praxis-sonnenquell.de</div>
  </div>
</div>

<!-- Inside spread -->
<div class="abs sheet" style="left:582px;top:1195px;width:538px;height:572px">
  <div class="abs" style="left:6px;top:6px;width:526px;height:560px;border:3px solid var(--mint-frame)"></div>
  <div class="abs" style="left:268px;top:6px;width:3px;height:560px;background:var(--mint-frame)"></div>

  <div class="abs it" style="left:28px;top:26px;width:205px;font-size:12px;line-height:1.45;border-left:2px solid var(--mint);padding-left:6px">
    Sie suchen schöne und <span class="hl">hochwertig ausgestattete Räume</span> in zentraler Lage für Therapie, Coaching oder Seminare?
  </div>
  <div class="abs it" style="left:52px;top:98px;width:183px;font-size:12px;line-height:1.45;text-align:right;border-right:2px solid var(--mint);padding-right:6px">
    Sie möchten <span class="hl">zeitlich flexibel</span> arbeiten und Ihre monatlichen <span class="hl">Fixkosten niedrig</span> halten?
  </div>
  <div class="abs banner" style="left:14px;top:182px;width:234px;height:44px;padding:8px 14px;font-size:12px;line-height:1.3">Unsere Praxis am Sonnenquell<br>bietet Ihnen genau das.</div>

  <div class="abs box" style="left:12px;top:246px;width:250px;height:148px;padding:8px 10px">
    <h3 style="font-size:12px;margin-bottom:4px">Die Praxis</h3>
    <p class="small">Die Praxis liegt direkt am Sendlinger Tor, ist sehr ruhig und bietet einen wunderschönen Blick ins Grüne. In ihr stehen fünf frisch renovierte und hochwertig ausgestattete Therapieräume sowie zwei Seminarräume zur Verfügung. An welchem Tag, zu welcher Uhrzeit und für wie viele Stunden Sie diese mieten, können Sie entscheiden, ganz so wie es Ihr Bedarf von Woche zu Woche oder auch für das ganze Jahr verlangt.</p>
  </div>
  <div class="abs box" style="left:12px;top:404px;width:250px;height:142px;padding:8px 10px">
    <h3 style="font-size:12px;margin-bottom:4px">An wen richtet sich unser Angebot?</h3>
    <p class="small">Unser Angebot richtet sich an Ärzte, Psychologen, Psychotherapeuten, Heilpraktiker für Psychotherapie (HeilprG) sowie Coaches und Supervisoren mit vergleichbarem und zertifiziertem Hintergrund. Darüber hinaus stehen die Räume auch für Seminare, Workshops oder Gruppenangebote zur Verfügung.</p>
  </div>

  <div class="abs" style="left:288px;top:22px;width:226px">
    <h3 style="font-size:12px;margin-bottom:4px">Die Räume</h3>
    <p class="small" style="margin-bottom:6px">Verschiedene Preismodelle bieten Ihnen je nach Bedarf volle Flexibilität:</p>
    <ul class="list small">
      <li>Sie können Räume entweder für einzelne Stunden oder im Abonnement mieten.</li>
      <li>Bei der Miete von einzelnen Stunden fallen keinerlei laufende Kosten an.</li>
      <li>Über ein Abonnement bieten wir Ihnen sehr attraktive Preise ab einer Stunde pro Woche.</li>
      <li>Sie können dadurch selbst bestimmen ob und in welcher Höhe Ihnen monatliche Fixkosten entstehen und welches Modell für Sie am besten geeignet ist.</li>
    </ul>
  </div>
  <span class="abs" style="left:474px;top:16px;width:30px;height:30px;border:2px solid #d8d8d8"></span>
  <div class="abs room-card" style="left:290px;top:236px;width:218px;height:128px">
    <div class="photo-room" role="img" aria-label="Foto: Therapieraum mit Sessel und Fensterfront" style="width:104px;flex:none"></div>
    <div class="txt"><div class="name">Therapieraum</div><div class="feat">Bequeme Sessel, höhenverstellbarer Schreibtisch, Schreibtischstuhl, Luftfilter, großzügige Fensterfront</div><div class="price">ab 17,⁰⁰ €/h</div></div>
  </div>
  <div class="abs room-card" style="left:290px;top:378px;width:218px;height:128px">
    <div class="txt" style="width:114px"><div class="name">Seminarraum</div><div class="feat">Flipchart, hochwertige Bestuhlung, Beamer, Hepa 13 Luftfilter, großzügige Fensterfront</div><div class="price">ab 17,⁰⁰ €/h</div></div>
    <div class="photo-seminar" role="img" aria-label="Foto: Seminarraum mit Stuhlreihen und Flipchart" style="flex:1"></div>
  </div>
  <p class="abs small" style="left:290px;top:516px;width:224px">Die genauen Konditionen, Bilder und alle weiteren Informationen finden Sie auf unserer Website <b>www.praxis-sonnenquell.de</b></p>
</div>

<!-- One-pager -->
<div class="abs sheet" style="left:262px;top:1877px;width:681px;height:963px">
  <div class="abs photo" role="img" aria-label="Foto: heller Raum mit zwei grauen Sesseln, Blumenvase und Seminarbereich" style="left:0;top:0;width:681px;height:300px"></div>
  <div class="abs" style="left:0;top:0;width:681px;height:118px;background:rgba(255,255,255,.88)"></div>
  <div class="abs brand" style="left:40px;top:50px;font-size:30px;gap:16px">
    <span class="brand-mark" style="width:54px;height:54px"></span><span>Praxis am<br>Sonnenquell</span>
  </div>
  <div class="abs" style="left:464px;top:48px;font-size:11px;line-height:1.45">Lindenweg 22<br>80337 München<br>kontakt@praxis-sonnenquell.de<br>www.praxis-sonnenquell.de</div>
  <svg class="abs" style="left:0;top:260px" width="681" height="120" viewBox="0 0 681 120">
    <polygon points="360,60 681,20 681,120 300,120" fill="#ffffff"/>
    <polygon points="0,0 372,0 330,100 0,100" fill="#5cbd9d" opacity=".85"/>
    <polygon points="0,100 330,100 300,120 0,120" fill="#ffffff"/>
  </svg>
  <div class="abs it" style="left:40px;top:296px;font-size:25px;font-weight:900;color:#fff;line-height:1.2">Flexible Raummiete<br>im Herzen von München</div>
  <div class="abs it" style="left:402px;top:302px;width:250px;font-size:10.5px;line-height:1.45;color:var(--mint);border-left:2px solid var(--mint);padding-left:6px">Sie suchen schöne und <b style="color:var(--ink)">hochwertig ausgestattete Räume</b> in zentraler Lage für Therapie, Coaching oder Seminare?</div>
  <div class="abs it" style="left:432px;top:360px;width:218px;font-size:10.5px;line-height:1.45;color:var(--mint);border-left:2px solid var(--mint);padding-left:6px">Sie möchten zeitlich <b style="color:var(--ink)">flexibel</b> arbeiten und Ihre monatlichen <b style="color:var(--ink)">Fixkosten niedrig</b> halten?</div>

  <div class="abs" style="left:40px;top:418px;width:286px">
    <h3 style="font-size:16px;margin-bottom:6px">An wen richtet sich unser Angebot?</h3>
    <p style="font-size:11px;line-height:1.6;text-align:justify">Unser Angebot richtet sich an Ärzte, Psychologen, Psychotherapeuten, Heilpraktiker für Psychotherapie (HeilprG) sowie Coaches und Supervisoren mit vergleichbarem und zertifiziertem Hintergrund. Darüber hinaus stehen die Räume auch für Seminare, Workshops oder Gruppenangebote zur Verfügung.</p>
  </div>
  <div class="abs" style="left:352px;top:398px;width:292px">
    <h3 style="font-size:16px;margin-bottom:6px">Die Praxis</h3>
    <p style="font-size:11px;line-height:1.6;text-align:justify">Die Praxis liegt direkt am Sendlinger Tor, ist sehr ruhig und bietet einen wunderschönen Blick ins Grüne. In ihr stehen fünf frisch renovierte und hochwertig ausgestattete Therapieräume sowie zwei Seminarräume zur Verfügung. An welchem Tag, zu welcher Uhrzeit und für wie viele Stunden Sie diese mieten, können Sie entscheiden, ganz so wie es Ihr Bedarf von Woche zu Woche oder auch für das ganze Jahr verlangt.</p>
  </div>

  <div class="abs" style="left:28px;top:580px;width:622px;height:236px;border:3px solid var(--mint-pale)"></div>
  <div class="abs" style="left:40px;top:594px;width:290px">
    <h3 style="font-size:16px;margin-bottom:6px">Die Räume</h3>
    <p style="font-size:11px;line-height:1.5;margin-bottom:6px">Unsere Preismodelle bieten je nach Bedarf volle Flexibilität:</p>
    <ul class="list" style="font-size:11px;line-height:1.55">
      <li>Sie können Räume entweder für einzelne Stunden oder im Abonnement mieten.</li>
      <li>Bei der Miete von einzelnen Stunden fallen keinerlei laufende Kosten an.</li>
      <li>Über ein Abonnement bieten wir Ihnen sehr attraktive Preise ab einer Stunde pro Woche.</li>
      <li>Sie können dadurch selbst bestimmen ob und in welcher Höhe Ihnen monatliche Fixkosten entstehen und welches Modell für Sie am besten geeignet ist.</li>
    </ul>
  </div>
  <div class="abs room-card" style="left:352px;top:590px;width:286px;height:102px">
    <div class="photo-room" role="img" aria-label="Foto: Therapieraum mit Sessel und Fensterfront" style="width:122px;flex:none"></div>
    <div class="txt"><div class="name" style="font-size:15px">Therapieraum</div><div class="feat" style="font-size:9.5px">Bequeme Sessel, höhenverstellbarer Schreibtisch, Schreibtischstuhl, Luftfilter, großzügige Fensterfront</div><div class="price" style="font-size:14px">ab 17,⁰⁰ €/h</div></div>
  </div>
  <div class="abs room-card" style="left:352px;top:704px;width:286px;height:102px">
    <div class="txt" style="width:164px"><div class="name" style="font-size:15px">Seminarraum</div><div class="feat" style="font-size:9.5px">Flipchart, hochwertige Bestuhlung, Beamer, Hepa 13 Luftfilter, großzügige Fensterfront</div><div class="price" style="font-size:14px">ab 17,⁰⁰ €/h</div></div>
    <div class="photo-seminar" role="img" aria-label="Foto: Seminarraum mit Stuhlreihen" style="flex:1"></div>
  </div>

  <div class="abs box" style="left:28px;top:826px;width:622px;height:114px;padding:12px 24px">
    <p class="it" style="font-size:11.5px;line-height:1.5"><b>Bei Fragen</b>, für weitere Informationen oder zur <b>Vereinbarung einer Besichtigung</b> – gerne auch virtuell über Video – kontaktieren Sie uns:</p>
    <div class="abs it" style="left:24px;top:58px;font-size:11.5px;line-height:1.5"><div class="hl">Carla Brenner-Voss</div>Email: kontakt@praxis-sonnenquell.de<br>Tel.: 0176 40218857</div>
    <div class="abs it" style="left:270px;top:58px;font-size:11.5px;line-height:1.5"><div class="hl">Tobias Voss</div>Email: kontakt@praxis-sonnenquell.de<br>Tel.: 0177 3095126</div>
    <span class="abs" style="right:30px;top:60px;width:34px;height:34px;border:2px solid #a8a8a8"></span>
  </div>
</div>

</body>
</html>
```